Etikett für einen Rosé Wein
Zielgruppe
Wir sind ein Weingut und benötigen ein neues Etikett für unseren Muskattrollinger Rosé. Unsere Kunden sind eher traditionelle Weinkäufer.
Aufgabenstellung
Format:
Höhe: 9 cm
Breite: 11 cm
Da es nur ein Vorderetikett gibt, müssen alle relevanten Angaben (Hersteller, Alkohol, Inhalt in L, Rebsorte, etc.) enthalten sein. (siehe Flaschenabbildung anbei)
WÜRTTEMBERG
2019er
Muskattrollinger Rosé
DEUTSCHER QUALITÄTSWEIN
11,0 % Vol.
0,75 l
Enthält Sulfite
A.P.Nr. 58127364
Abfüller
Straße / PLZ / Ort / Tel.
Der Flaschenverschluss ist schwarz d.h. das neue Etikettendesign sollte dazu passen.
Bisher ist der Hintergrund des Weinetiketts schwarz. Dies muss jedoch nicht so bleiben.
Im Anhang finden Sie außerdem ein Plakat. Ggf. können Sie für das Flaschendesign einige nostalgische Elemente davon übernehmen.

```html
<!DOCTYPE html>
<html lang="de">
<head>
<meta charset="utf-8">
<title>Muskattrollinger Rosé – Etikett</title>
<link href="https://fonts.googleapis.com/css2?family=Tinos:wght@400;700&family=Mrs+Saint+Delafield&display=swap" rel="stylesheet">
<style>
  :root {
    --backdrop: #e2e2e2;
    --label-black: #000000;
    --ink-white: #ffffff;
    --art-light: #d9d9d9;
    --art-dark: #3a3a3a;
  }
  html, body {
    margin: 0;
    padding: 0;
    width: 1200px;
    height: 900px;
    overflow: hidden;
    background: var(--backdrop);
  }
  .wine-label {
    position: absolute;
    left: 105px;
    top: 45px;
    width: 990px;
    height: 810px;
    background: var(--label-black);
    color: var(--ink-white);
    font-family: "Tinos", "Times New Roman", serif;
  }
  .wine-label > * {
    position: absolute;
    margin: 0;
    white-space: nowrap;
  }
  .region {
    left: 0; right: 0; top: 28px;
    text-align: center;
    font-weight: 700;
    font-size: 30px;
    letter-spacing: 0.5px;
  }
  .vintage {
    left: 0; right: 0; top: 76px;
    text-align: center;
    font-weight: 700;
    font-size: 22px;
  }
  .variety {
    left: 0; right: 0; top: 170px;
    text-align: center;
    font-family: "Mrs Saint Delafield", cursive;
    font-weight: 400;
    font-size: 94px;
    line-height: 85px;
  }
  .variety span { display: block; }
  .estate-art {
    left: 326px;
    top: 400px;
    width: 372px;
    height: 190px;
  }
  .alcohol {
    left: 232px;
    top: 670px;
    width: 100px;
    text-align: center;
    font-weight: 700;
    font-size: 24px;
    line-height: 31px;
  }
  .quality {
    left: 356px;
    top: 690px;
    width: 300px;
    text-align: center;
    font-weight: 700;
    font-size: 18px;
  }
  .volume {
    left: 687px;
    top: 683px;
    font-weight: 700;
    font-size: 24px;
  }
  .legal {
    left: 0; right: 0; top: 734px;
    padding-left: 22px;
    text-align: center;
    font-size: 12.5px;
    line-height: 15.5px;
  }
  .legal span { display: block; }
</style>
</head>
<body>
  <section class="wine-label">
    <h2 class="region">WÜRTTEMBERG</h2>
    <p class="vintage">2019er</p>
    <h1 class="variety"><span>Muskattrollinger</span><span>Rosé</span></h1>
    <svg class="estate-art" viewBox="0 0 372 190" role="img" aria-label="Engraved illustration of a winery estate among vineyard rows">
      <defs>
        <radialGradient id="estateTone" cx="50%" cy="55%" r="60%">
          <stop offset="0%" stop-color="var(--art-light)"/>
          <stop offset="100%" stop-color="var(--art-dark)"/>
        </radialGradient>
      </defs>
      <ellipse cx="186" cy="95" rx="186" ry="95" fill="url(#estateTone)"/>
    </svg>
    <p class="alcohol">11,0 %<br>Vol.</p>
    <p class="quality">DEUTSCHER QUALITÄTSWEIN</p>
    <p class="volume">0,75 l</p>
    <p class="legal">
      <span>A.P.Nr. 58127364</span>
      <span>Abfüller D-BWK 172</span>
      <span>vermarket durch: Lukas Renner Straße / PLZ / Ort / Tel.</span>
    </p>
  </section>
</body>
</html>
```